Business Card Design Project

I need a business card designed from scratch. I have an existing logo that I can upload in Illustrator for modification or redesign.

The Company is called Query Lanterns http://querylanterns.com.au and we provide Search Engine Optimization services to Australian businesses. The current logo signifies an increase in visitors, profits etc...

There are no restrictions as to the redesign - colours, style etc are all open to change.

Cards will be full colour and one sided printed at http://www.cardmoxel.com.au so check their requirements for file format and sizes etc.

I will expect all original files upon completion of project.

Target Market(s)

Any business with a web site looking to improve their search engine rankings

Industry/Entity Type

Business

Requirements
Must have
• I like modern, sleek designs. Clean, not fussy, uncluttered.

```html
<!DOCTYPE html>
<html lang="en">
<head>
<meta charset="utf-8">
<title>Query Lanterns – Business Card</title>
<link href="https://fonts.googleapis.com/css2?family=PT+Sans:wght@400;700&display=swap" rel="stylesheet">
<style>
  :root {
    --brand-blue: #1a73b8;
    --band-blue: #1b72b9;
    --band-shade: #145a93;
    --card-white: #ffffff;
    --ink: #2a2a2a;
    --backdrop: #e9e6e2;
  }
  * { box-sizing: border-box; margin: 0; padding: 0; }
  html, body {
    width: 1200px; height: 460px; overflow: hidden;
    background: var(--backdrop);
    font-family: "PT Sans", Arial, sans-serif;
  }
  .stage { position: relative; width: 1200px; height: 460px; }
  .card {
    position: absolute; width: 540px; height: 310px;
    border-radius: 16px; overflow: hidden;
  }
  .card--front { left: 36px; top: 74px; background: var(--card-white); }
  .card--back { left: 624px; top: 76px; background: var(--brand-blue); }

  .brand {
    position: absolute; top: 72px; left: 0; width: 100%;
    display: flex; justify-content: center; align-items: center; gap: 12px;
  }
  .brand__dot {
    width: 16px; height: 16px; border-radius: 50%; background: var(--brand-blue);
  }
  .brand__name {
    font-weight: 700; font-size: 40px; color: var(--brand-blue); letter-spacing: -0.5px;
  }

  .bands { position: absolute; inset: 0; }

  .holder {
    position: absolute; top: 182px; left: 0; width: 100%;
    text-align: center; color: #fff; font-size: 14px;
  }
  .holder__name { font-weight: 700; font-size: 17px; }

  .contacts {
    position: absolute; top: 220px; left: 98px;
    display: grid; grid-template-columns: 116px auto; row-gap: 2px; column-gap: 14px;
    font-size: 13.5px; color: var(--ink);
  }
  .contact { display: flex; align-items: center; gap: 6px; }
  .contact svg { width: 10px; height: 10px; fill: var(--brand-blue); }

  .address {
    position: absolute; top: 263px; left: 0; width: 100%;
    text-align: center; color: #fff; font-size: 14px;
  }

  .back-brand {
    position: absolute; top: 96px; left: 0; width: 100%;
    display: flex; justify-content: center; align-items: center; gap: 12px;
  }
  .back-brand__dot {
    width: 20px; height: 20px; border-radius: 50%; border: 5px solid #fff;
  }
  .back-brand__name { font-weight: 700; font-size: 38px; color: #fff; }
  .back-web {
    position: absolute; top: 222px; left: 0; width: 100%;
    text-align: center; color: #fff; font-size: 14px; letter-spacing: 1.2px;
  }
</style>
</head>
<body>
<main class="stage">
  <section class="card card--front">
    <div class="brand">
      <span class="brand__dot"></span>
      <span class="brand__name">Query Lanterns</span>
    </div>

    <svg class="bands" viewBox="0 0 540 310" aria-hidden="true">
      <path d="M518,176 Q532,172 540,166 L540,196 Q530,200 518,204 Z" fill="var(--band-shade)"/>
      <path d="M0,182 Q260,186 524,172 L526,206 Q260,216 0,214 Z" fill="var(--band-blue)"/>
      <path d="M0,214 Q4,206 10,200 L10,216 Z" fill="var(--band-shade)"/>
      <path d="M518,252 Q532,248 540,242 L540,272 Q530,276 518,280 Z" fill="var(--band-shade)"/>
      <path d="M0,258 Q260,262 524,248 L526,282 Q260,292 0,292 Z" fill="var(--band-blue)"/>
      <path d="M0,292 Q4,284 10,278 L10,294 Z" fill="var(--band-shade)"/>
    </svg>

    <p class="holder"><span class="holder__name">Your Name</span> Title</p>

    <div class="contacts">
      <span class="contact">
        <svg viewBox="0 0 10 10"><path d="M2,0.5 L4,2.5 L3,4 Q4.5,6 6,7 L7.5,6 L9.5,8 L8,9.5 Q3,9 0.5,2 Z"/></svg>
        098 765 4321
      </span>
      <span class="contact">
        <svg viewBox="0 0 10 10"><path d="M0,1.5 H10 V8.5 H0 Z M0.6,2 L5,5.5 L9.4,2 Z" fill-rule="evenodd"/></svg>
        enquiry@querylanterns.com.au
      </span>
      <span class="contact">
        <svg viewBox="0 0 10 10"><path d="M2.5,0 H7.5 V10 H2.5 Z M3.3,1 V7.5 H6.7 V1 Z" fill-rule="evenodd"/></svg>
        098 765 4321
      </span>
      <span class="contact">
        <svg viewBox="0 0 10 10"><circle cx="5" cy="5" r="4.5"/></svg>
        www.querylanterns.com.au
      </span>
    </div>

    <p class="address">00Floor Street, City Name State Name, Contry Name</p>
  </section>

  <section class="card card--back">
    <div class="back-brand">
      <span class="back-brand__dot"></span>
      <span class="back-brand__name">Query Lanterns</span>
    </div>
    <p class="back-web">www.querylanterns.com.au</p>
  </section>
</main>
</body>
</html>
```